Build a landing page to promote a service (dialler consultation and support).

We are a call centre consultation firm and we need a landing page to promote a service. The service is Tormalux dialler consultation and support.
If you do not know what Tormalux is, please do some quick "Zorvex" research for more information.
The landing page will be promoted with a paid advertisement, so we want something that is simple, and explains exactly what service we offer.
There are two objectives for the landing page:
1) A "call to action" which directs the user to a contact page, including a form plus all of our contact details.
2) A form for them viewers to enter their details to get a "FREE" quote for their project. This form should be placed on the main page.
Notes:
The call to action will require the viewer to enter their name, email, phone number as well as a description of their request. There will also need to be a drop down menu for the type of quote. This menu should have the following options:
1) Tormalux support
2) Tormalux hosting
3) Tormalux customisation
4) Other
We need 2 pages in total:
1) Main landing page
This is the home page. It will need to clearly indicate our services and our key selling features.
Services:
* Tormalux support
* Tormalux hosting
* Tormalux customisation
Key Selling Features:
* Australian based
* PCI complaint
* 10+ years of dialler and call centre experience
* we run a sister company which is a highly reputable 40 seat call centre, so we know first hand about call centre technology.
The main landing page will have an "about us" section with a few paragraphs about how we got started.
-------------------------------------------------------------------------
2) Contact page
All of our contact details will live on this page, as well as a contact form.
Other notes:
We will be self hosting the landing page.
We already have a domain name.
The design must be clean and incorporate our logo, as well as it's colours. (Logo attached)
We want a fully function HTML landing page, not just a "PSD" design.
The page must be mobile optimised.
Anyone using Tormalux software.

```html
<!DOCTYPE html>
<html lang="en">
<head>
<meta charset="utf-8">
<title>Quellcall – Contact Us</title>
<link href="https://fonts.googleapis.com/css2?family=Lato:wght@400;700&display=swap" rel="stylesheet">
<style>
:root{
  --brand-blue:#1a7cc4;
  --brand-teal:#22b096;
  --ink:#2b2b2b;
  --muted:#666;
  --form-bg:#f7faee;
  --field-border:#d9dccb;
  --footer-bg:#111;
  --white:#fff;
  --land:#e4e2d9;
  --land-soft:#ebe9e1;
  --water:#aecbe6;
  --brand-gradient:linear-gradient(90deg,var(--brand-blue),var(--brand-teal));
}
*{box-sizing:border-box;margin:0;padding:0}
html,body{width:1200px;height:709px;overflow:hidden}
body{font-family:'Lato',sans-serif;color:var(--ink);position:relative;background:var(--land)}
.location-map{position:absolute;left:0;top:0;width:1200px;height:663px;
  background:
    radial-gradient(ellipse 520px 260px at 1000px 640px,var(--water) 0%,var(--water) 55%,rgba(174,203,230,0) 100%),
    radial-gradient(ellipse 260px 160px at 1180px 120px,#c9dcec 0%,rgba(201,220,236,0) 100%),
    linear-gradient(160deg,var(--land-soft) 0%,var(--land) 55%,#dfe3df 100%)}
.top-strip{position:absolute;left:0;top:0;width:1200px;height:5px;background:var(--brand-gradient)}
.site-header{position:absolute;left:0;top:5px;width:1200px;height:125px;background:rgba(255,255,255,.6)}
.brand{position:absolute;left:74px;top:12px;width:160px;text-align:center}
.brand-mark{display:block;width:66px;height:66px;border-radius:50%;background:var(--brand-teal);margin:0 auto 6px}
.brand-name{font-size:27px;font-weight:700;color:var(--brand-blue);letter-spacing:.3px}
.main-nav a{position:absolute;top:35px;height:49px;line-height:49px;font-size:18.5px;color:var(--ink);text-decoration:none}
.main-nav .is-active{left:537px;width:97px;text-align:center;border-radius:25px;background:var(--brand-teal);color:var(--white);box-shadow:0 3px 6px rgba(0,0,0,.2)}
.contact-form{position:absolute;left:75px;top:149px;width:362px;height:472px;background:var(--form-bg)}
.form-title{height:60px;line-height:60px;text-align:center;background:var(--brand-gradient);color:var(--white);font-size:26px;font-weight:700}
.field{position:absolute;left:22px;width:317px;height:46px;border:1px solid var(--field-border);background:var(--form-bg);
  font-family:'Lato',sans-serif;font-size:14.5px;color:var(--muted);padding:0 16px}
.field::placeholder{color:var(--muted)}
textarea.field{height:78px;padding-top:13px;resize:none}
.submit-btn{position:absolute;left:75px;top:389px;width:212px;height:49px;border:0;background:var(--brand-gradient);
  color:var(--white);font-family:'Lato',sans-serif;font-size:22px;font-weight:700}
.info-card{position:absolute;left:561px;top:179px;width:316px;height:179px;background:var(--white);font-size:18.5px;line-height:24px;font-style:normal}
.info-card::after{content:"";position:absolute;left:167px;bottom:-14px;border:14px solid transparent;border-bottom:0;border-top-color:var(--white)}
.info-row{position:absolute;left:38px;display:flex;gap:8px}
.info-row svg{flex:none;margin-top:3px}
.site-footer{position:absolute;left:0;top:663px;width:1200px;height:46px;background:var(--footer-bg);color:var(--white);font-size:13px;line-height:46px}
.footer-meta{position:absolute;left:74px}
.footer-meta .sep{margin:0 14px;color:#888}
.page-code{position:absolute;left:1149px;font-weight:700}
</style>
</head>
<body>
<div class="location-map" role="img" aria-label="Street map of the office area, with land to the left and the bay to the lower right"></div>
<div class="top-strip"></div>

<header class="site-header">
  <div class="brand"><span class="brand-mark"></span><span class="brand-name">Quellcall</span></div>
  <nav class="main-nav">
    <a class="is-active" href="#">Home</a>
    <a href="#" style="left:658px">About Us</a>
    <a href="#" style="left:785px">Services</a>
    <a href="#" style="left:901px">Features</a>
    <a href="#" style="left:1021px">Contact Us</a>
  </nav>
</header>

<form class="contact-form">
  <h2 class="form-title">Contact Form</h2>
  <input class="field" style="top:89px" placeholder="Name">
  <input class="field" style="top:155px" placeholder="Email">
  <input class="field" style="top:220px" placeholder="Phone Number">
  <textarea class="field" style="top:286px" placeholder="Description"></textarea>
  <button class="submit-btn" type="submit">Submit</button>
</form>

<address class="info-card">
  <div class="info-row" style="top:30px">
    <svg width="15" height="20" viewBox="0 0 15 20"><path d="M7.5 0A7.5 7.5 0 0 0 0 7.5C0 13 7.5 20 7.5 20S15 13 15 7.5A7.5 7.5 0 0 0 7.5 0zm0 10.5a3 3 0 1 1 0-6 3 3 0 0 1 0 6z" fill="#333"/></svg>
    <span>2471 Harbor Crest Lane.<br>Brightwater,<br>NY 11092.</span>
  </div>
  <div class="info-row" style="top:124px">
    <svg width="13" height="20" viewBox="0 0 13 20"><rect x="1" y="1" width="11" height="18" rx="2" fill="none" stroke="#333" stroke-width="2"/><rect x="3" y="3" width="7" height="11" fill="#333"/><circle cx="6.5" cy="16.3" r="1.1" fill="#333"/></svg>
    <span>1-800 555 0142</span>
  </div>
</address>

<footer class="site-footer">
  <span class="footer-meta">© 2018<span class="sep">|</span>www.quellcall.com</span>
  <span class="page-code">M1</span>
</footer>
</body>
</html>
```